Letterhead, stationery and email signature for construction business

I need the letterhead, stationery and email signature designs for a construction business. I want them to have a corporate feel to them.

I've attached the logo for reference.

```html
<!DOCTYPE html>
<html lang="en">
<head>
<meta charset="utf-8">
<title>HTML Email Signature – Bramwell Projects</title>
<link rel="stylesheet" href="https://fonts.googleapis.com/css2?family=Cinzel:wght@600&family=Montserrat:wght@500&family=Open+Sans:wght@400&family=Raleway:wght@700&display=swap">
<style>
  :root {
    --bg: #ffffff;
    --ink-title: #3a3a3a;
    --brand-blue: #2d5aa8;
    --ink-body: #6a6a6a;
    --ink-role: #4a4a4a;
    --rule: #8a8a8a;
    --photo-a: #c9d3dc;
    --photo-b: #6f7781;
  }
  * { margin: 0; padding: 0; box-sizing: border-box; }
  html, body { width: 1200px; height: 1200px; overflow: hidden; background: var(--bg); }
  .canvas { position: relative; width: 1200px; height: 1200px; }

  .page-title {
    position: absolute; top: 188px; left: 0; width: 1200px;
    text-align: center;
    font-family: "Cinzel", serif; font-weight: 600;
    font-size: 44px; line-height: 56px; letter-spacing: 1px;
    color: var(--ink-title);
  }

  .portrait {
    position: absolute; left: 188px; top: 498px;
    width: 202px; height: 202px; border-radius: 50%;
    background: radial-gradient(circle at 45% 40%, var(--photo-a) 0%, #a9b2bb 50%, var(--photo-b) 100%);
  }

  .divider {
    position: absolute; left: 427px; top: 496px;
    width: 1.5px; height: 208px; background: var(--rule);
  }

  .details { position: absolute; left: 466px; top: 500px; }
  .details .name {
    font-family: "Raleway", sans-serif; font-weight: 700;
    font-size: 24px; line-height: 28px; color: var(--brand-blue); letter-spacing: 0.2px;
  }
  .details .role {
    font-family: "Open Sans", sans-serif; font-size: 20px;
    line-height: 26px; color: var(--ink-role);
  }
  .details .address {
    margin-top: 16px;
    font-family: "Montserrat", sans-serif; font-weight: 500;
    font-size: 18px; line-height: 23px; color: var(--ink-body);
  }
  .contact-list { list-style: none; margin-top: 6px; }
  .contact-list li {
    display: flex; align-items: center; gap: 6px;
    font-family: "Montserrat", sans-serif; font-weight: 500;
    font-size: 18.5px; line-height: 26.5px; color: var(--ink-body);
  }
  .contact-list svg { width: 18px; height: 18px; flex: none; }

  .company-name {
    position: absolute; left: 761px; top: 572px; width: 251px;
    text-align: center;
    font-family: "Montserrat", sans-serif; font-weight: 500;
    font-size: 24px; line-height: 30px; color: var(--ink-body);
  }

  .social { position: absolute; left: 835px; top: 626px; display: flex; gap: 4px; }
  .social span { width: 22px; height: 22px; border-radius: 50%; background: var(--brand-blue); display: block; }
</style>
</head>
<body>
<div class="canvas">
  <h1 class="page-title">HTML EMAIL SIGNATURE</h1>

  <div class="portrait" role="img" aria-label="Portrait photograph of the company owner"></div>
  <div class="divider"></div>

  <div class="details">
    <div class="name">DANIEL HARTWELL</div>
    <div class="role">Owner</div>
    <div class="address">Ashby House, 42 Kingsley<br>Rd, London SE14 7QP</div>
    <ul class="contact-list">
      <li>
        <svg viewBox="0 0 24 24" aria-hidden="true"><path fill="#2d5aa8" d="M6.6 10.8a15.1 15.1 0 0 0 6.6 6.6l2.2-2.2c.3-.3.7-.4 1-.2 1.1.4 2.3.6 3.6.6.6 0 1 .4 1 1V20c0 .6-.4 1-1 1A17 17 0 0 1 3 4c0-.6.4-1 1-1h3.5c.6 0 1 .4 1 1 0 1.3.2 2.5.6 3.6.1.3 0 .7-.2 1z"/></svg>
        (555) 018-4420
      </li>
      <li>
        <svg viewBox="0 0 24 24" aria-hidden="true"><rect x="2" y="5" width="20" height="14" fill="none" stroke="#2d5aa8" stroke-width="2"/><path d="M2 5l10 8 10-8M2 19l7-7M22 19l-7-7" fill="none" stroke="#2d5aa8" stroke-width="2"/></svg>
        info@bramwell.com
      </li>
      <li>
        <svg viewBox="0 0 24 24" aria-hidden="true"><g fill="none" stroke="#2d5aa8" stroke-width="1.8"><circle cx="12" cy="12" r="9.5"/><ellipse cx="12" cy="12" rx="4" ry="9.5"/><path d="M2.5 12h19M4 7h16M4 17h16"/></g></svg>
        www.bramwell.com
      </li>
    </ul>
  </div>

  <div class="company-name">Bramwell Projects</div>

  <div class="social" aria-label="Social links">
    <span></span><span></span><span></span><span></span>
  </div>
</div>
</body>
</html>
```